IT Company requires new Business Card design.

Over the years we have had a few different business card designs. We are now due for new cards across the board for all staff. We felt this would be a good time to start fresh with a new design. Our traditional card simply had our details on the front, and a list of services on the back. We don't particularly need the list of services, we have had cards where the only thing on the rear of the card was our logo.
Feel free to be creative, we would like our tag line "Complete IT Management" to appear at some point, doesn't necessarily have to be with the logo.
I have attached samples and drafts of various previous cards we have used over the years.

```html
<!DOCTYPE html>
<html lang="en">
<head>
<meta charset="utf-8">
<title>Harbor Networks – Business Card</title>
<link rel="stylesheet" href="https://fonts.googleapis.com/css2?family=Open+Sans:wght@400;600;800&display=swap">
<style>
  :root {
    --page-bg: #e9e7e3;
    --card-top: #3a3b3d;
    --card-bottom: #252628;
    --text-main: #f2f2f2;
    --text-soft: #c9cbcd;
    --accent-line-top: #7c93a6;
    --accent-line-bottom: #4a5560;
    --brand-silver: #d9dadc;
  }
  * { margin: 0; padding: 0; box-sizing: border-box; }
  html, body {
    width: 1200px; height: 720px; overflow: hidden;
    background: var(--page-bg);
    font-family: "Open Sans", Arial, sans-serif;
  }
  .sheet {
    width: 1200px; height: 720px;
    display: flex; align-items: center; justify-content: center; gap: 40px;
  }
  .card {
    position: relative;
    width: 525px; height: 300px;
    background: linear-gradient(160deg, var(--card-top), var(--card-bottom));
    border-radius: 3px;
    box-shadow: 0 6px 18px rgba(0,0,0,.25);
    color: var(--text-main);
    overflow: hidden;
  }

  /* Front */
  .brand-block {
    position: absolute; left: 36px; top: 122px;
    display: flex; align-items: center; gap: 12px;
  }
  .brand-square {
    width: 38px; height: 38px;
    background: var(--brand-silver);
  }
  .brand-text { display: flex; flex-direction: column; }
  .brand-name {
    font-weight: 800; font-size: 22px; line-height: 1.05;
    color: var(--brand-silver); text-transform: uppercase; letter-spacing: .5px;
  }
  .brand-tagline {
    margin-top: 4px;
    font-size: 7.5px; letter-spacing: 2.2px; text-transform: uppercase;
    color: var(--text-soft);
  }
  .divider {
    position: absolute; left: 300px; top: 28px;
    width: 2px; height: 168px;
    background: linear-gradient(var(--accent-line-top), var(--accent-line-bottom));
  }
  .contact {
    position: absolute; left: 316px; top: 26px;
    font-size: 11.5px; color: var(--text-main);
  }
  .person-name { font-weight: 800; font-size: 15px; line-height: 1.2; }
  .person-role { font-size: 10.5px; color: var(--text-soft); margin-bottom: 10px; }
  .contact-list { list-style: none; }
  .contact-list li {
    display: flex; align-items: center; gap: 7px;
    line-height: 18px;
  }
  .contact-list svg { width: 11px; height: 11px; fill: var(--text-main); flex: none; }
  .address { margin-top: 10px; line-height: 16px; }

  /* Back */
  .back-brand {
    position: absolute; left: 0; right: 0; top: 100px;
    display: flex; justify-content: center; align-items: center; gap: 16px;
  }
  .back-brand .brand-square { width: 54px; height: 54px; }
  .back-brand .brand-name { font-size: 32px; }
  .back-url {
    position: absolute; left: 0; right: 0; bottom: 30px;
    text-align: center; font-size: 13px; color: var(--text-main);
  }
</style>
</head>
<body>
<main class="sheet">

  <section class="card card-front" aria-label="Business card front">
    <div class="brand-block">
      <span class="brand-square"></span>
      <div class="brand-text">
        <span class="brand-name">Harbor<br>Networks</span>
        <span class="brand-tagline">Complete IT Management</span>
      </div>
    </div>

    <div class="divider"></div>

    <div class="contact">
      <p class="person-name">Marcus Hale</p>
      <p class="person-role">Operation Manager</p>
      <ul class="contact-list">
        <li>
          <svg viewBox="0 0 12 12" aria-hidden="true"><path d="M2.5 1h2l1 3-1.3.9a6 6 0 0 0 2.9 2.9L8 6.5l3 1v2c0 .8-.7 1.5-1.5 1.5A8.5 8.5 0 0 1 1 2.5C1 1.7 1.7 1 2.5 1z"/></svg>
          08 5550 1234
        </li>
        <li>
          <svg viewBox="0 0 12 12" aria-hidden="true"><path d="M3.5 0h5c.6 0 1 .4 1 1v10c0 .6-.4 1-1 1h-5c-.6 0-1-.4-1-1V1c0-.6.4-1 1-1zm.5 1.5v7.5h4V1.5z"/></svg>
          0400 555 018
        </li>
        <li>
          <svg viewBox="0 0 12 12" aria-hidden="true"><path d="M3 0h5v3H3zM1 4h10c.6 0 1 .4 1 1v4H0V5c0-.6.4-1 1-1zm2 6h6v2H3z"/></svg>
          08 5550 1235
        </li>
        <li>
          <svg viewBox="0 0 12 12" aria-hidden="true"><path d="M0 2h12v8H0zm1 1 5 3.5L11 3z" fill-rule="evenodd"/></svg>
          marcus@harbornetworks.com.au
        </li>
        <li>
          <svg viewBox="0 0 12 12" aria-hidden="true"><circle cx="6" cy="6" r="5.2" fill="none" stroke="#f2f2f2" stroke-width="1.2"/><path d="M1 6h10M6 .8c2 2.8 2 7.6 0 10.4M6 .8c-2 2.8-2 7.6 0 10.4" fill="none" stroke="#f2f2f2" stroke-width=".9"/></svg>
          www.harbornetworks.com.au
        </li>
      </ul>
      <p class="address">Unit 4 12 Seaview Way<br>Bayford WA 6000</p>
    </div>
  </section>

  <section class="card card-back" aria-label="Business card back">
    <div class="back-brand">
      <span class="brand-square"></span>
      <span class="brand-name">Harbor Networks</span>
    </div>
    <p class="back-url">www.harbornetworks.com.au</p>
  </section>

</main>
</body>
</html>
```